KBT Business Cards

We require business cards for our business. We would like a matte black back to the card, with our logo centred in the middle. The front side of the card is open to design.

Target Market(s)

Clients looking for legal services (professional)

Industry/Entity Type

Legal

Contact Information for Business Card

Doran Kelbrath
Partner
Mobile: 0461 738 524
Email: doran@kbtlaw.co
Website: www.kbtlaw.co
Level 3, 118 Wendmore Street
Sydney NSW 2000

Font styles to use
Other font styles liked:
• Avenir

Colors
f04a50
ffffff
1b1b1b

Requirements
Must have
• Black back with logo included in the centre of the card.
• Our font is Avenir.

```html
<!DOCTYPE html>
<html lang="en">
<head>
<meta charset="utf-8">
<title>KBT Legal — Business Cards</title>
<link rel="stylesheet" href="https://fonts.googleapis.com/css2?family=Nunito+Sans:wght@300;400;700;800&display=swap">
<style>
  :root {
    --stage: #1c1c1c;
    --paper: #e9e9e9;
    --ink: #1b1b1b;
    --band: #151515;
    --crimson: #b71c3c;
    --crimson-deep: #7d1428;
    --text-light: #e6e6e6;
    --back-card: #0f0f0f;
    --back-mark: #242424;
  }
  * { box-sizing: border-box; margin: 0; padding: 0; }
  html, body {
    width: 1200px; height: 1200px; overflow: hidden;
    background: var(--stage);
    font-family: "Nunito Sans", "Avenir", sans-serif;
  }
  .card {
    position: absolute; left: 227px; width: 746px; height: 424px;
    overflow: hidden;
  }
  .card--front { top: 136px; background: var(--paper); }
  .card--back { top: 640px; background: var(--back-card); }

  .brand {
    position: absolute; left: 40px; top: 82px;
    display: flex; align-items: center; gap: 18px;
  }
  .brand__square { width: 30px; height: 30px; background: var(--crimson); }
  .brand__name {
    font-weight: 800; font-size: 54px; letter-spacing: 1px;
    color: var(--ink); line-height: 1;
  }

  .contact-band {
    position: absolute; left: 0; top: 222px; width: 100%; height: 169px;
    background: var(--band);
  }
  .contact-band__accent { position: absolute; inset: 0; }

  .person { position: absolute; left: 35px; top: 12px; }
  .person__name {
    font-weight: 700; font-size: 24px; letter-spacing: 1px; color: var(--crimson);
  }
  .person__role {
    font-weight: 400; font-size: 17px; letter-spacing: .5px; color: var(--text-light);
    margin-top: 2px;
  }

  .contact-list {
    position: absolute; left: 35px; top: 84px; list-style: none;
    font-weight: 300; font-size: 18px; letter-spacing: .6px; color: var(--text-light);
  }
  .contact-list li { display: flex; align-items: center; gap: 9px; height: 24px; }
  .contact-list svg { width: 18px; height: 18px; flex: none; }
  .contact-list .hl { color: var(--crimson); }

  .address {
    position: absolute; left: 248px; top: 108px;
    font-style: normal; font-weight: 300; font-size: 18px; letter-spacing: .6px;
    color: var(--text-light); line-height: 24px;
  }

  .back-brand {
    position: absolute; left: 50%; top: 50%; transform: translate(-50%, -50%);
    display: flex; align-items: center; gap: 20px;
  }
  .back-brand__square { width: 34px; height: 34px; background: var(--back-mark); }
  .back-brand__name {
    font-weight: 800; font-size: 60px; letter-spacing: 1px; line-height: 1;
    color: var(--back-mark);
  }
</style>
</head>
<body>
  <section class="card card--front">
    <div class="brand">
      <span class="brand__square"></span>
      <span class="brand__name">KBT Legal</span>
    </div>

    <div class="contact-band">
      <svg class="contact-band__accent" viewBox="0 0 746 169" preserveAspectRatio="none" aria-hidden="true">
        <defs>
          <linearGradient id="accentFill" x1="0" y1="0" x2="1" y2="1">
            <stop offset="0" stop-color="#c4213f"/>
            <stop offset="1" stop-color="#7d1428"/>
          </linearGradient>
        </defs>
        <polygon points="609,0 746,0 746,169 629,169 709,89" fill="url(#accentFill)"/>
      </svg>

      <div class="person">
        <div class="person__name">Doran Kelbrath</div>
        <div class="person__role">Partner</div>
      </div>

      <ul class="contact-list">
        <li>
          <svg viewBox="0 0 18 18" aria-hidden="true"><circle cx="9" cy="9" r="9" fill="var(--crimson)"/><path d="M5 7.5c0-1.3 1.8-2.3 4-2.3s4 1 4 2.3l-1.5.6-.6-1.2H7.1l-.6 1.2zM6.3 9h5.4l.8 3.8H5.5z" fill="#151515"/></svg>
          <span>0461 738 524</span>
        </li>
        <li>
          <svg viewBox="0 0 18 18" aria-hidden="true"><circle cx="9" cy="9" r="9" fill="var(--crimson)"/><rect x="4.5" y="5.8" width="9" height="6.4" fill="none" stroke="#151515" stroke-width="1.2"/><path d="M4.5 6l4.5 3.6L13.5 6" fill="none" stroke="#151515" stroke-width="1.2"/></svg>
          <span>doran@kbtlaw.co</span>
        </li>
        <li>
          <svg viewBox="0 0 18 18" aria-hidden="true"><circle cx="9" cy="9" r="9" fill="var(--crimson)"/><circle cx="9" cy="9" r="5" fill="none" stroke="#151515" stroke-width="1.2"/><path d="M4 9h10M9 4c-2 3-2 7 0 10M9 4c2 3 2 7 0 10" fill="none" stroke="#151515" stroke-width="1"/></svg>
          <span>www.<span class="hl">kbtlaw</span>.co</span>
        </li>
      </ul>

      <address class="address">
        Level 3, 118 Wendmore Street<br>
        Sydney NSW 2000
      </address>
    </div>
  </section>

  <section class="card card--back">
    <div class="back-brand">
      <span class="back-brand__square"></span>
      <span class="back-brand__name">KBT Legal</span>
    </div>
  </section>
</body>
</html>
```